Bramwell Corner Sports Pub. Where the locals go!!

We are creating a sports pub. We are needing a fun website that offers our menu along with an event page and general info. We have some attached links that we really like:
https://www.dunmorrows.example/
https://www.cafepelindra.example/
https://www.quillstoneyx.example/
We are doing a pirate theme but that is because the area we are in. We would like to see a pirate like in our logo doing something like drinking real time similar to the dunmorrows website above.
Target Market(s)
Sports Fans
Industry/Entity Type
Pub, Bar, Restaurant
Coding
Coded - Design and coding required
Number of Pages Required
3 page
Font styles to use
Other font styles liked:
- see uploads
Look and feel

```html
<!DOCTYPE html>
<html lang="en">
<head>
<meta charset="utf-8">
<title>Bramwell Corner Sports Pub</title>
<link rel="stylesheet" href="https://fonts.googleapis.com/css2?family=Rye&family=Open+Sans:wght@400;600&display=swap">
<style>
:root{
  --cream:#faf7ee;
  --ink:#222222;
  --text:#3a3a3a;
  --gold:#d9c48a;
  --line:#d8d4c8;
  --footer:#2b2b2b;
  --white:#ffffff;
}
*{margin:0;padding:0;box-sizing:border-box}
html,body{width:1200px;height:2976px;overflow:hidden}
body{background:var(--cream);font-family:"Open Sans",sans-serif;color:var(--text);position:relative}
.abs{position:absolute}
.display{font-family:"Rye",serif;color:var(--ink);font-weight:400}

/* hero */
.hero{left:0;top:0;width:1200px;height:540px;overflow:hidden}
.hero-photo{position:absolute;inset:0;background:
  radial-gradient(ellipse 260px 340px at 600px 360px,#b88534 0%,#7a4e1c 45%,transparent 75%),
  radial-gradient(ellipse 400px 300px at 180px 250px,#5d4630 0%,transparent 70%),
  linear-gradient(180deg,#1f1c1c 0%,#2a2522 50%,#1b1d26 100%)}
.hero-curve{position:absolute;left:0;top:0}
.menu-toggle{left:113px;top:22px;width:36px;height:36px;border:2px solid var(--white);border-radius:50%}
.menu-toggle span{position:absolute;left:9px;width:15px;height:2px;background:var(--white)}
.brand{left:500px;top:30px;width:200px;text-align:center;display:flex;flex-direction:column;align-items:center;gap:8px}
.brand-dot{width:54px;height:54px;border-radius:50%;background:var(--cream)}
.brand-name{font-family:"Open Sans",sans-serif;font-weight:600;font-size:15px;color:var(--white)}
.social{top:32px;width:18px;height:18px;border-radius:50%;border:2px solid var(--white)}
.hero-title{left:0;top:312px;width:1200px;text-align:center;color:var(--white);font-size:58px;line-height:66px}
.scroll-mouse{left:591px;top:472px;width:22px;height:34px;border:2px solid var(--white);border-radius:11px}
.scroll-mouse::after{content:"";position:absolute;left:8px;top:6px;width:2px;height:10px;background:var(--white)}

/* shared */
h2.display{font-size:62px;line-height:1}
.btn{display:block;width:170px;height:45px;background:var(--ink);color:var(--white);font-size:15px;line-height:45px;text-align:center;box-shadow:5px 5px 0 var(--gold);letter-spacing:.3px}
p.body{font-size:16px;line-height:30px}

/* about */
.about-title{left:112px;top:592px}
.about-copy{left:112px;top:682px;width:520px}
.about-copy p+p{margin-top:17px}
.about-btn{left:112px;top:966px}
.about-photo{left:769px;top:587px;width:319px;height:393px;background:linear-gradient(160deg,#3e2a1c 0%,#8a5a28 40%,#c58b45 65%,#3a2718 100%)}
.frame-line{background:#7d7d7d}

/* menu */
.menu-title{left:0;top:1124px;width:1200px;text-align:center}
.menu-item{width:454px;height:120px}
.menu-item .name{position:absolute;left:2px;top:0;font-size:17px;color:var(--ink);text-transform:uppercase}
.menu-item .price{position:absolute;right:0;top:-4px;font-size:17px;color:var(--ink)}
.menu-item .dots{position:absolute;left:132px;right:42px;top:13px;border-top:1px dotted var(--line)}
.menu-item .desc{position:absolute;left:0;top:34px;font-size:16px;line-height:28px}
.menu-btn{left:513px;top:1783px}
.menu-deco{left:955px;top:1752px;width:245px;height:240px;background:radial-gradient(circle,#dedbd2 0%,rgba(222,219,210,0) 70%)}

/* gallery */
.gallery-title{left:0;top:1907px;width:1200px;text-align:center}
.gallery{left:0;top:2007px;width:1200px;height:346px;display:flex}
.gallery div{flex:1}
.g1{background:linear-gradient(160deg,#2b2a26,#6b4a3a 50%,#3a2a22)}
.g2{background:linear-gradient(160deg,#8a4a2a,#c8823a 45%,#2c3a6a)}
.g3{background:linear-gradient(160deg,#3a2a22,#6a3a2a 50%,#1f1b18)}
.arrows{left:535px;top:2398px}

/* contact */
.contact-title{left:0;top:2462px;width:1200px;text-align:center}
.contact-photo{left:112px;top:2579px;width:319px;height:269px;background:linear-gradient(160deg,#5a1a14,#a8402a 40%,#3a2018)}
.info-head{font-size:21px;color:var(--ink)}
.info-text{font-size:16px;line-height:29px}
.icon{position:absolute}

/* footer */
.footer{left:0;top:2922px;width:1200px;height:54px;background:var(--footer);color:var(--white);text-align:center;font-size:16px;line-height:54px}
</style>
</head>
<body>

<header class="abs hero">
  <div class="hero-photo" role="img" aria-label="Two glasses of beer raised in a toast inside a warmly lit pub"></div>
  <svg class="hero-curve" width="1200" height="540" viewBox="0 0 1200 540">
    <path d="M0 471 Q600 620 1200 471 L1200 540 L0 540 Z" fill="#faf7ee"/>
  </svg>
  <div class="abs menu-toggle">
    <span style="top:11px"></span><span style="top:16px"></span><span style="top:21px"></span>
  </div>
  <div class="abs brand">
    <div class="brand-dot"></div>
    <div class="brand-name">Bramwell Corner Sports Pub</div>
  </div>
  <div class="abs social" style="left:994px" aria-label="Social link"></div>
  <div class="abs social" style="left:1028px" aria-label="Social link"></div>
  <div class="abs social" style="left:1070px" aria-label="Social link"></div>
  <h1 class="abs display hero-title">Welcome to<br>Bramwell Corner Sports Pub</h1>
  <div class="abs scroll-mouse"></div>
</header>

<section>
  <h2 class="abs display about-title">About Us</h2>
  <div class="abs about-copy">
    <p class="body">Lorem ipsum dolor sit amet, consectetur adipiscing elit, sed do eius mod tempor incididunt ut labore et dolore magna aliqua. Quis ipsum suspendisse ultrices gravida. Risus commodo viverra maecenas ac cumsan lacus vel facilisis.</p>
    <p class="body">Lorem ipsum dolor sit amet, consectetur adipiscing elit, sed do eius mod tempor incididunt ut labore et dolore magna aliqua. Quis ipsum suspendisse ultrices gravida. Risus commodo viverra maecenas ac cumsan lacus vel facilisis.</p>
  </div>
  <a class="abs btn about-btn">LEARN MORE</a>
  <div class="abs frame-line" style="left:726px;top:842px;width:1px;height:190px"></div>
  <div class="abs frame-line" style="left:726px;top:1023px;width:185px;height:1px"></div>
  <div class="abs about-photo" role="img" aria-label="Long wooden bar counter with taps and screens showing sports"></div>
</section>

<section>
  <h2 class="abs display menu-title">Our Menu</h2>

  <div class="abs menu-item" style="left:112px;top:1248px"><span class="name">Lorem Ipsum</span><span class="dots"></span><span class="price">$15</span><p class="desc">Sed do eiusmod tempor incididunt ut labore et<br>dolore magna aliqua suspendisse ultrices gravida.</p></div>
  <div class="abs menu-item" style="left:635px;top:1248px"><span class="name">Lorem Ipsum</span><span class="dots"></span><span class="price">$15</span><p class="desc">Sed do eiusmod tempor incididunt ut labore et<br>dolore magna aliqua suspendisse ultrices gravida.</p></div>
  <div class="abs menu-item" style="left:112px;top:1377px"><span class="name">Lorem Ipsum</span><span class="dots"></span><span class="price">$15</span><p class="desc">Sed do eiusmod tempor incididunt ut labore et<br>dolore magna aliqua suspendisse ultrices gravida.</p></div>
  <div class="abs menu-item" style="left:635px;top:1377px"><span class="name">Lorem Ipsum</span><span class="dots"></span><span class="price">$15</span><p class="desc">Sed do eiusmod tempor incididunt ut labore et<br>dolore magna aliqua suspendisse ultrices gravida.</p></div>
  <div class="abs menu-item" style="left:112px;top:1505px"><span class="name">Lorem Ipsum</span><span class="dots"></span><span class="price">$15</span><p class="desc">Sed do eiusmod tempor incididunt ut labore et<br>dolore magna aliqua suspendisse ultrices gravida.</p></div>
  <div class="abs menu-item" style="left:635px;top:1505px"><span class="name">Lorem Ipsum</span><span class="dots"></span><span class="price">$15</span><p class="desc">Sed do eiusmod tempor incididunt ut labore et<br>dolore magna aliqua suspendisse ultrices gravida.</p></div>
  <div class="abs menu-item" style="left:112px;top:1634px"><span class="name">Lorem Ipsum</span><span class="dots"></span><span class="price">$15</span><p class="desc">Sed do eiusmod tempor incididunt ut labore et<br>dolore magna aliqua suspendisse ultrices gravida.</p></div>
  <div class="abs menu-item" style="left:635px;top:1634px"><span class="name">Lorem Ipsum</span><span class="dots"></span><span class="price">$15</span><p class="desc">Sed do eiusmod tempor incididunt ut labore et<br>dolore magna aliqua suspendisse ultrices gravida.</p></div>

  <a class="abs btn menu-btn">LEARN MORE</a>
  <div class="abs menu-deco" role="img" aria-label="Faint pirate emblem decoration"></div>
</section>

<section>
  <h2 class="abs display gallery-title">Gallery</h2>
  <div class="abs gallery">
    <div class="g1" role="img" aria-label="Fans cheering at the bar during a football game"></div>
    <div class="g2" role="img" aria-label="Colourful bar interior with memorabilia on the ceiling"></div>
    <div class="g3" role="img" aria-label="Dining area with leather booth and framed photos on brick wall"></div>
  </div>
  <svg class="abs arrows" width="130" height="16" viewBox="0 0 130 16" fill="none" stroke="#c9a45c" stroke-width="2">
    <path d="M46 8 H2 M9 2 L2 8 L9 14"/>
    <path d="M84 8 H128 M121 2 L128 8 L121 14"/>
  </svg>
</section>

<section>
  <h2 class="abs display contact-title">Contact Us</h2>
  <div class="abs frame-line" style="left:72px;top:2532px;width:185px;height:1px"></div>
  <div class="abs frame-line" style="left:72px;top:2532px;width:1px;height:190px"></div>
  <div class="abs contact-photo" role="img" aria-label="Busy pub crowd under red string lights"></div>

  <svg class="icon" style="left:503px;top:2589px" width="14" height="20" viewBox="0 0 14 20"><path d="M7 0C3 0 0 3 0 7c0 5 7 13 7 13s7-8 7-13c0-4-3-7-7-7zm0 10a3 3 0 1 1 0-6 3 3 0 0 1 0 6z" fill="#222"/></svg>
  <div class="abs info-head" style="left:538px;top:2589px">Address</div>
  <p class="abs info-text" style="left:538px;top:2632px">Bramwell Corner Sports Pub,<br>Address comes here</p>

  <svg class="icon" style="left:503px;top:2720px" width="18" height="18" viewBox="0 0 24 24"><path d="M6.6 10.8a15 15 0 0 0 6.6 6.6l2.2-2.2c.3-.3.7-.4 1-.2 1.1.4 2.3.6 3.6.6.6 0 1 .4 1 1V20c0 .6-.4 1-1 1C10.6 21 3 13.4 3 4c0-.6.4-1 1-1h3.5c.6 0 1 .4 1 1 0 1.3.2 2.5.6 3.6.1.3 0 .7-.2 1z" fill="#222"/></svg>
  <div class="abs info-head" style="left:538px;top:2717px">Call Us</div>
  <p class="abs info-text" style="left:538px;top:2760px">+1 555-014-2290 or<br>+1 555-014-2291</p>

  <svg class="icon" style="left:752px;top:2589px" width="14" height="20" viewBox="0 0 14 20"><path d="M7 0C3 0 0 3 0 7c0 5 7 13 7 13s7-8 7-13c0-4-3-7-7-7zm0 10a3 3 0 1 1 0-6 3 3 0 0 1 0 6z" fill="#222"/></svg>
  <div class="abs info-head" style="left:787px;top:2589px">Hours</div>
  <p class="abs info-text" style="left:787px;top:2632px">Kitchen closes at 9pm Tuesday–Saturday<br>and 6:30pm Sunday.</p>
  <p class="abs info-text" style="left:787px;top:2718px">Tuesday—Thursday: 4pm—10pm<br>Friday: 3pm—11pm<br>Saturday: 11am—11pm<br>Sunday: 11am—7pm</p>
</section>

<footer class="abs footer">2023 Bramwell Corner Sports Pub. All Rights Reserved.</footer>

</body>
</html>
```